Halvery Construction Group Website

Need a dynamic corporate website that can be built on with time. We want to get our information out to the world and have a place where customers can submit requests for proposals.

Target Market(s)

Custom home owners and buyers. Architects and Real Estate Agents.

Industry/Entity Type

Construction

Number of Pages Required

3 page

Font styles to use
Serif
Sans Serif

Requirements
Must have
• Company logo, about, company contact information, biography, contact, projects,
• Sleek, modern, clean, attractive design.
• Online form customers can use for filling out a request for project proposal.
• Professional network hyperlink.
• Uses www.halveryconstructiongroup.example

```html
<!DOCTYPE html>
<html lang="en">
<head>
<meta charset="utf-8">
<title>Halvery Construction Group</title>
<link rel="stylesheet" href="https://fonts.googleapis.com/css2?family=Exo+2:wght@400;500;600&family=Arimo:wght@400;700&display=swap">
<style>
:root{
  --brand:#0a56a8;
  --brand-dark:#08468c;
  --brand-light:#2e9fd6;
  --ink:#111111;
  --muted:#8a8a8a;
  --body:#555555;
  --panel:#efefef;
  --white:#ffffff;
  --line:#d4d4d4;
}
*{margin:0;padding:0;box-sizing:border-box}
html,body{width:1200px;height:2980px;overflow:hidden}
body{position:relative;background:var(--white);font-family:"Arimo",Arial,sans-serif;color:var(--body)}
.abs{position:absolute}
.heading{font-family:"Exo 2",sans-serif;font-weight:500;font-size:44px;color:var(--ink);letter-spacing:.5px;text-transform:uppercase}
.heading span{color:var(--brand)}
.center{left:0;width:1200px;text-align:center}
.pill{background:var(--brand);color:var(--white);border-radius:30px;display:flex;align-items:center;justify-content:center;font-family:"Exo 2",sans-serif;font-size:21px;text-transform:uppercase}

/* hero */
.hero{left:0;top:0;width:1200px;height:640px;background:linear-gradient(180deg,#dfe7f1 0%,#eef2f6 45%,#b9c2cc 80%,#7d8a96 100%)}
.hero-call{left:880px;top:38px;color:#1d2f52;font-family:"Exo 2",sans-serif}
.hero-call small{display:block;font-size:15px;font-weight:600;margin-left:52px}
.hero-call b{display:block;font-size:29px;font-weight:600;color:var(--brand-dark);margin-left:52px;margin-top:-2px}
.hero-brand{top:148px;left:0;width:1200px;display:flex;justify-content:center;align-items:center;gap:16px}
.hero-brand i{width:72px;height:72px;background:var(--brand);display:block}
.hero-brand span{font-family:"Exo 2",sans-serif;font-size:44px;font-weight:500;color:var(--brand);text-transform:uppercase}
.hero-title{top:284px;font-family:"Exo 2",sans-serif;font-size:48px;font-weight:600;color:var(--ink)}
.hero-sub{top:352px;font-size:21px;color:var(--ink)}
.hero-cta{left:472px;top:402px;width:262px;height:60px;font-family:"Arimo",sans-serif;font-size:20px}

/* nav */
.nav{left:0;top:640px;width:1200px;height:60px;background:var(--brand)}
.nav a{position:absolute;top:0;height:60px;line-height:60px;color:var(--white);text-decoration:none;font-size:16px;text-transform:uppercase}
.nav .active{left:78px;width:114px;background:var(--brand-light);text-align:center}

/* welcome */
.intro{top:812px;left:250px;width:700px;text-align:center;font-size:13px;line-height:26px;color:var(--muted)}
.service{top:888px;width:240px;text-align:center}
.service .badge{width:126px;height:126px;border-radius:50%;background:var(--brand);margin:0 auto;display:flex;align-items:center;justify-content:center}
.service h3{margin-top:30px;font-size:16px;font-weight:400;color:var(--brand);text-transform:uppercase}
.service p{margin-top:8px;font-size:13px;line-height:25px;color:var(--muted);padding:0 10px}

/* about */
.about{left:0;top:1190px;width:1200px;height:408px;background:var(--panel)}
.about-text{left:80px;top:1328px;width:740px;font-size:13px;line-height:27px;color:var(--muted)}
.about-text p+p{margin-top:4px}

/* testimonial */
.quote-band{left:0;top:1598px;width:1200px;height:408px;background:linear-gradient(180deg,#0b55a6 0%,#0d5cae 60%,#1e5f9e 100%)}
.quote-text{left:160px;top:1786px;width:880px;text-align:center;color:var(--white);font-size:14px;line-height:28px}
.client{left:590px;top:1862px;color:var(--white)}
.client b{display:block;font-family:"Exo 2",sans-serif;font-weight:400;font-size:18px;text-transform:uppercase}
.client small{display:block;font-size:13px;margin-top:6px}

/* projects */
.project{top:2120px;width:250px;text-align:center}
.project .shot{width:250px;height:190px}
.project h4{margin-top:18px;font-weight:400;font-size:18px;color:var(--brand)}
.project p{margin-top:8px;font-size:13px;color:#444}

/* contact */
.contact{left:0;top:2436px;width:1200px;height:492px;background:var(--panel)}
.contact-text{left:80px;top:2550px;width:540px;font-size:14px;line-height:26px;color:#444}
.info{left:78px;font-size:13px;color:#444;line-height:26px}
.info svg{position:absolute;left:0;top:4px}
.info div{margin-left:38px}
.info .lead{color:var(--brand);font-size:14px}
.social{top:2840px;width:38px;height:38px;border:2px solid var(--brand);border-radius:50%}
.field{left:626px;width:502px;height:52px;background:var(--white);border:1px solid var(--line);font-size:13px;color:var(--muted);padding:14px 22px}
.field.focus{border:2px solid var(--brand)}
.submit{left:626px;top:2806px;width:502px;height:52px;font-size:20px}

.footer{left:0;top:2928px;width:1200px;height:52px;background:var(--brand);color:var(--white);text-align:center;line-height:52px;font-size:13px}
</style>
</head>
<body>

<!-- hero -->
<div class="abs hero" role="img" aria-label="Photograph of a modern multi-storey glass office building under a pale sky"></div>
<div class="abs hero-call">
  <svg class="abs" style="left:2px;top:8px" width="40" height="40" viewBox="0 0 24 24"><path fill="#1f4f8f" d="M6.6 10.8a15.1 15.1 0 0 0 6.6 6.6l2.2-2.2c.3-.3.7-.4 1-.2 1.1.4 2.3.6 3.6.6.6 0 1 .4 1 1V20c0 .6-.4 1-1 1C10.6 21 3 13.4 3 4c0-.6.4-1 1-1h3.5c.6 0 1 .4 1 1 0 1.3.2 2.5.6 3.6.1.3 0 .7-.2 1z"/></svg>
  <small>Call Us now</small>
  <b>123-456-7890</b>
</div>
<div class="abs hero-brand"><i></i><span>Halvery</span></div>
<div class="abs center hero-title">Halvery Construction Group, Inc.</div>
<div class="abs center hero-sub">Lorem Ipsum Is Simply Dummy Text Of The Printing</div>
<div class="abs pill hero-cta">CONTACT US NOW</div>

<!-- nav -->
<nav class="abs nav">
  <a class="active" href="#">Home</a>
  <a style="left:230px" href="#">About Us</a>
  <a style="left:372px" href="#">Services</a>
  <a style="left:512px" href="#">Projects</a>
  <a style="left:658px" href="#">Contact Us</a>
  <svg class="abs" style="left:1100px;top:17px" width="26" height="26" viewBox="0 0 24 24"><circle cx="10" cy="10" r="6.5" fill="none" stroke="#0c1d3a" stroke-width="3"/><path d="M15 15l6 6" stroke="#0c1d3a" stroke-width="3.5" stroke-linecap="round"/></svg>
</nav>

<!-- welcome -->
<h2 class="abs center heading" style="top:742px">Welcome to <span>Halvery Construction Group</span></h2>
<p class="abs intro">Lorem Ipsum is simply dummy text of the printing and typesetting industry. &nbsp;Lorem Ipsum has been the industry's standard dummy text ever since the 1500s, when an unknown printer.</p>

<div class="abs service" style="left:76px">
  <div class="badge" style="background:var(--brand-light)">
    <svg width="70" height="70" viewBox="0 0 24 24"><path fill="#fff" d="M12 3 1.5 12.5h3V21h5.5v-6h4v6h5.5v-8.5h3z"/></svg>
  </div>
  <h3 style="color:var(--ink)">Tenant Improvement</h3>
  <p>Lorem Ipsum is simply dummy text of the printing and typesetting industry. Lorem Ipsum has.</p>
</div>
<div class="abs service" style="left:346px">
  <div class="badge">
    <svg width="70" height="70" viewBox="0 0 24 24" fill="#fff"><path d="M6 2h1.5v20H6zM2 4h17v1.4H2zM17.5 5.4h1v3h-1z"/><rect x="11" y="11" width="10" height="11"/><g fill="#0a56a8"><rect x="12.5" y="13" width="2" height="2"/><rect x="16.5" y="13" width="2" height="2"/><rect x="12.5" y="17" width="2" height="2"/><rect x="16.5" y="17" width="2" height="2"/></g></svg>
  </div>
  <h3>Warehouse Construction</h3>
  <p>Lorem Ipsum is simply dummy text of the printing and typesetting industry. Lorem Ipsum has.</p>
</div>
<div class="abs service" style="left:616px">
  <div class="badge">
    <svg width="66" height="66" viewBox="0 0 24 24"><path fill="#fff" d="M10.3 1h3.4l.6 3 2 .9 2.6-1.7 2.4 2.4-1.7 2.6.9 2 3 .6v3.4l-3 .6-.9 2 1.7 2.6-2.4 2.4-2.6-1.7-2 .9-.6 3h-3.4l-.6-3-2-.9-2.6 1.7-2.4-2.4 1.7-2.6-.9-2-3-.6v-3.4l3-.6.9-2-1.7-2.6 2.4-2.4 2.6 1.7 2-.9z"/><circle cx="12" cy="12" r="5" fill="#0a56a8"/><circle cx="12" cy="12" r="2.6" fill="#fff"/></svg>
  </div>
  <h3>Project Management</h3>
  <p>Lorem Ipsum is simply dummy text of the printing and typesetting industry. Lorem Ipsum has.</p>
</div>
<div class="abs service" style="left:892px">
  <div class="badge">
    <svg width="70" height="70" viewBox="0 0 24 24" fill="#fff"><path d="M12 3 1.5 11h2.5l8-6 8 6h2.5z"/><path d="M5 12v9h14v-9l-7-5.2z"/><rect x="8" y="14" width="3" height="3" fill="#0a56a8"/><rect x="13" y="14" width="3" height="7" fill="#0a56a8"/></svg>
  </div>
  <h3>Renovations</h3>
  <p>Lorem Ipsum is simply dummy text of the printing and typesetting industry. Lorem Ipsum has.</p>
</div>

<!-- about -->
<section class="abs about"></section>
<h2 class="abs heading" style="left:80px;top:1264px">About <span>Halvery Construction Group</span></h2>
<div class="abs about-text">
  <p>Lorem Ipsum is simply dummy text of the printing and typesetting industry. Lorem Ipsum has been the industry's standard dummy text ever since the 1500s, when an unknown printer took a galley of type.</p>
  <p>Lorem Ipsum is simply dummy text of the printing and typesetting industry. Lorem Ipsum has been the industry's standard dummy text ever since the 1500s, when an unknown printer took a galley of type and scrambled it to make a type specimen book. industry's standard dummy.</p>
</div>
<div class="abs pill" style="left:78px;top:1472px;width:178px;height:60px">Know More</div>
<div class="abs" style="left:908px;top:1326px;width:216px;height:206px;background:linear-gradient(160deg,#1c4fa0,#2e8fd6)"></div>

<!-- testimonial -->
<section class="abs quote-band" role="img" aria-label="Blue-tinted photograph of city office towers"></section>
<h2 class="abs center heading" style="top:1652px">What our <span style="color:var(--white)">Client Say</span></h2>
<svg class="abs" style="left:576px;top:1722px" width="56" height="56" viewBox="0 0 56 56"><circle cx="28" cy="28" r="26" fill="#fff"/><text x="28" y="44" text-anchor="middle" font-family="Georgia,serif" font-size="40" font-weight="700" fill="#0a56a8">&#8220;</text></svg>
<svg class="abs" style="left:76px;top:1790px" width="32" height="32" viewBox="0 0 32 32"><circle cx="16" cy="16" r="14" fill="none" stroke="#fff" stroke-width="1.5"/><path d="M18 10l-6 6 6 6" fill="none" stroke="#fff" stroke-width="1.8"/></svg>
<svg class="abs" style="left:1092px;top:1790px" width="32" height="32" viewBox="0 0 32 32"><circle cx="16" cy="16" r="14" fill="none" stroke="#fff" stroke-width="1.5"/><path d="M14 10l6 6-6 6" fill="none" stroke="#fff" stroke-width="1.8"/></svg>
<p class="abs quote-text">Lorem Ipsum is simply dummy text of the printing and typesetting industry. Lorem Ipsum has been the industry's standard dummy text ever since the 1500s, when an unknown printer took a galley of type and.</p>
<div class="abs" style="left:488px;top:1856px;width:80px;height:80px;border-radius:50%;background:linear-gradient(180deg,#c9cdd3,#3c4656)" role="img" aria-label="Client portrait photograph"></div>
<div class="abs client"><b>Client Name</b><small>(Something.com)</small></div>

<!-- projects -->
<h2 class="abs center heading" style="top:2036px">Latest <span>Project</span></h2>
<div class="abs project" style="left:78px"><div class="shot" style="background:linear-gradient(180deg,#7fb0e0,#c9d6df 60%,#6c7a68)" role="img" aria-label="Photograph of a residential tower block"></div><h4>Lorem Ipsum is simply</h4><p>Lorem Ipsum is simply dummy text</p></div>
<div class="abs project" style="left:344px"><div class="shot" style="background:linear-gradient(180deg,#1d49a6,#4d78c4 55%,#b9a98f)" role="img" aria-label="Photograph of a modern building entrance at dusk"></div><h4>Lorem Ipsum is simply</h4><p>Lorem Ipsum is simply dummy text</p></div>
<div class="abs project" style="left:610px"><div class="shot" style="background:linear-gradient(135deg,#e9f1f8,#5a93d0 50%,#1b4e8c)" role="img" aria-label="Photograph of glass office towers against the sky"></div><h4>Lorem Ipsum is simply</h4><p>Lorem Ipsum is simply dummy text</p></div>
<div class="abs project" style="left:876px"><div class="shot" style="background:linear-gradient(180deg,#2f7fd0,#a6c6e0 55%,#5f8a4a)" role="img" aria-label="Photograph of a modern office building with lawn"></div><h4>Lorem Ipsum is simply</h4><p>Lorem Ipsum is simply dummy text</p></div>

<!-- contact -->
<section class="abs contact"></section>
<div class="abs" style="left:400px;top:2540px;width:420px;height:340px;background:radial-gradient(ellipse at center,#dcdcdc 0%,rgba(239,239,239,0) 70%)" role="img" aria-label="Faint world map"></div>
<h2 class="abs heading" style="left:80px;top:2480px">Contact <span>Us</span></h2>
<p class="abs contact-text">Lorem Ipsum is simply dummy text of the printing and typesetting industry. Lorem Ipsum has been the industry's standard dummy text ever since the 1500s, when an unknown printer took a galley of type.</p>
<div class="abs info" style="top:2660px">
  <svg width="24" height="20" viewBox="0 0 24 20"><path d="M1 3l7-2 8 2 7-2v16l-7 2-8-2-7 2z M8 1v16 M16 3v16" fill="none" stroke="#222" stroke-width="1.6"/></svg>
  <div class="lead">Lorem Ipsum is simply</div>
  <div>Lorem Ipsum is simply<br>dummy text of the printing</div>
</div>
<div class="abs info" style="top:2748px">
  <svg width="20" height="20" viewBox="0 0 24 24"><path fill="#222" d="M6.6 10.8a15.1 15.1 0 0 0 6.6 6.6l2.2-2.2c.3-.3.7-.4 1-.2 1.1.4 2.3.6 3.6.6.6 0 1 .4 1 1V20c0 .6-.4 1-1 1C10.6 21 3 13.4 3 4c0-.6.4-1 1-1h3.5c.6 0 1 .4 1 1 0 1.3.2 2.5.6 3.6.1.3 0 .7-.2 1z"/></svg>
  <div>Lorem Ipsum is simply</div>
</div>
<div class="abs info" style="top:2786px">
  <svg width="22" height="18" viewBox="0 0 22 18"><rect x="1" y="2" width="20" height="14" fill="none" stroke="#222" stroke-width="1.6"/><path d="M1 3l10 7 10-7" fill="none" stroke="#222" stroke-width="1.6"/></svg>
  <div>123-456-7890</div>
</div>
<a class="abs social" style="left:78px;background:var(--brand)" href="#" aria-label="Social profile one"></a>
<a class="abs social" style="left:122px" href="#" aria-label="Social profile two"></a>
<a class="abs social" style="left:166px" href="#" aria-label="Professional network profile"></a>

<div class="abs field focus" style="top:2504px">Name:</div>
<div class="abs field" style="top:2566px">E-Mail:</div>
<div class="abs field" style="top:2628px">Subject:</div>
<div class="abs field" style="top:2690px;height:104px">Message</div>
<div class="abs pill submit">Submit</div>

<footer class="abs footer">&copy; <b>Halvery Construction Group, Inc.</b> - 2016. All Rights Reserved</footer>

</body>
</html>
```